Landing Page and Logo for Auto-Blogging Platform

I created a platform that allows users to start a blog for their business, hobby, charity, etc. I need a landing page where users can learn about the platform, benefits of consistent blogging, SEO value, plans/pricing, etc. The landing page needs to have multiple call to action buttons encouraging the visitor to register/sign up for a free trial.

In addition to the landing page, I need a page for users to establish the settings for their blog. This page should be a fairly simple form, intended for the user to enter a few details to set up their blog:
1. Name of Blog
2. Up to 10 topics and/or keywords the blog should focus on
3. Theme: Color-scheme and logo upload for blog.

I have attached the specifications of the platform's functionality so you can better understand how it works, plans/pricing, etc.

I also need a logo for the business. The name of the platform is PostNook.

Target Market(s)

Website owners, bloggers, business owners

Industry/Entity Type

Technology, Internet, web design

Coding

Coded - Design and coding required

Number of Pages Required

2 page

Colors
0054AA
0677BA
7BADD7
CADEEF
E8F1F8
0094D4
00A9DD
6FCCEA
C7EBF8
E9F6FB

Requirements
Must have
• Eye-catching design but fairly light on content (keep it simple and brief.)
Nice to have
• Eye-catching yet simple design, clean and easy to understand what we are offering.
Should not have
• Too much “wordy” and confusing content.

```html
<!DOCTYPE html>
<html lang="en">
<head>
<meta charset="utf-8">
<title>PostNook – Auto-Blogging Platform</title>
<link rel="stylesheet" href="https://fonts.googleapis.com/css2?family=Roboto:wght@300;400;500;700;900&display=swap">
<style>
:root{
  --navy:#0a2a5c;
  --blue-deep:#0054AA;
  --blue:#0677BA;
  --blue-bright:#0094D4;
  --cyan:#00A9DD;
  --sky:#6FCCEA;
  --pale:#E8F1F8;
  --pale-2:#CADEEF;
  --ink:#1d2433;
  --grey:#6b7280;
  --line:#e3e8ef;
  --footer:#1f2023;
  --white:#fff;
}
*{box-sizing:border-box;margin:0;padding:0}
html,body{width:1200px;height:3592px;overflow:hidden}
body{font-family:"Roboto",Arial,sans-serif;color:var(--ink);background:var(--white);position:relative}
.section{position:absolute;left:0;width:1200px}
.abs{position:absolute}
.btn{display:inline-block;border-radius:24px;font-weight:500;font-size:15px;text-align:center;line-height:44px;height:44px;padding:0 26px;color:var(--white);background:var(--blue-deep)}
.brand{display:flex;align-items:center;gap:10px;font-weight:700;font-size:28px;color:var(--blue-deep)}
.brand-dot{width:30px;height:30px;border-radius:50%;background:var(--blue-deep)}

/* header */
.site-header{top:0;height:62px;background:var(--white);z-index:5}
.site-header .brand{position:absolute;left:112px;top:12px}
.nav{position:absolute;right:112px;top:0;height:62px;display:flex;align-items:center;gap:30px;font-size:15px;color:var(--ink)}
.nav .active{color:var(--blue-deep);font-weight:500;position:relative}
.nav .active:after{content:"";position:absolute;left:0;right:0;bottom:-8px;height:2px;background:var(--blue-deep)}
.nav .register{height:36px;line-height:36px;padding:0 24px;font-size:14px;margin-left:4px}

/* hero */
.hero{top:62px;height:620px}
.hero-photo{position:absolute;inset:0;background:linear-gradient(100deg,#05152f 0%,#0a2c5e 45%,#2c5b8c 70%,#0b2a52 100%)}
.hero-wave{position:absolute;left:0;bottom:0}
.hero h1{position:absolute;left:112px;top:140px;color:var(--white);font-weight:700;line-height:1}
.hero h1 .pre{display:block;font-size:44px;margin-bottom:18px}
.hero h1 .name{display:block;font-size:88px;font-weight:900}
.hero p{position:absolute;left:112px;top:318px;width:440px;color:#dfe8f4;font-size:16px;line-height:1.5}
.hero .btn{position:absolute;left:112px;top:414px}
.dots{position:absolute;left:570px;top:560px;display:flex;gap:8px}
.dots span{width:10px;height:10px;border-radius:50%;background:rgba(255,255,255,.5)}
.dots span:first-child{background:var(--white)}

/* about */
.about{top:682px;height:618px}
.monitor{position:absolute;left:80px;top:110px;width:520px;height:390px;border-radius:10px;background:linear-gradient(180deg,#e9edf2 0%,#cfd6df 100%)}
.section-title{font-size:32px;font-weight:400;color:var(--blue)}
.section-title b{font-weight:700;color:var(--navy)}
.about .section-title{position:absolute;left:700px;top:130px}
.about p{position:absolute;left:700px;top:186px;width:420px;font-size:15px;line-height:1.62;color:var(--grey)}
.about .btn{position:absolute;left:700px;top:450px}

/* plans */
.plans{top:1300px;height:600px;background:var(--pale)}
.center-title{position:absolute;left:0;width:1200px;text-align:center;font-size:32px;color:var(--blue)}
.center-title b{font-weight:700}
.plans .center-title{top:78px}
.plan{position:absolute;top:162px;width:308px;height:400px;background:var(--white);border-radius:6px;box-shadow:0 8px 24px rgba(0,84,170,.08);padding:34px 30px}
.plan.featured{top:150px;height:424px;background:var(--blue-deep);color:var(--white);padding-top:44px}
.plan .label{font-size:13px;font-weight:500;letter-spacing:.5px}
.plan .price{margin-top:22px;font-size:46px;font-weight:700}
.plan .price small{font-size:14px;font-weight:400;color:var(--blue-bright);vertical-align:top;margin-left:6px}
.plan.featured .price small{color:var(--sky)}
.plan .posts{margin-top:14px;font-size:15px;padding-bottom:20px;border-bottom:1px solid var(--line)}
.plan.featured .posts{border-color:rgba(255,255,255,.25)}
.plan ul{list-style:none;margin-top:18px}
.plan li{display:flex;align-items:center;gap:12px;font-size:14px;margin-bottom:14px}
.plan .btn{position:absolute;left:30px;bottom:30px;height:40px;line-height:40px;font-size:13px;font-weight:700;padding:0 24px}
.plan.featured .btn{background:var(--white);color:var(--blue-deep)}

/* benefits */
.benefits{top:1900px;height:520px}
.benefits .center-title{top:78px}
.benefit{position:absolute;top:198px;width:240px;text-align:center}
.benefit-icon{width:184px;height:184px;margin:0 auto;border-radius:50%;border:1px solid var(--pale-2);background:var(--white);display:flex;align-items:center;justify-content:center;box-shadow:0 6px 18px rgba(0,84,170,.08)}
.benefit-icon span{width:96px;height:96px;border-radius:50%;background:linear-gradient(180deg,var(--pale) 0%,var(--pale-2) 100%)}
.benefit.active .benefit-icon{background:var(--blue-deep);border-color:var(--blue-deep)}
.benefit.active .benefit-icon span{background:linear-gradient(180deg,#2a7bd0 0%,#0a62b8 100%)}
.benefit h3{margin-top:30px;font-size:22px;font-weight:700;color:var(--ink)}
.benefit p{margin-top:10px;font-size:13px;line-height:1.5;color:var(--grey)}
.arrow{position:absolute;top:272px;width:32px;height:32px;border-radius:50%;background:var(--blue-deep);display:flex;align-items:center;justify-content:center}
.arrow.prev{background:var(--white);border:1px solid var(--blue-deep)}

/* topics */
.topics{top:2420px;height:470px;background:linear-gradient(110deg,var(--blue-deep) 0%,var(--blue) 55%,var(--blue-bright) 100%)}
.topics h2{position:absolute;left:112px;top:86px;font-size:32px;font-weight:400;color:var(--white)}
.topics h2 b{font-weight:700}
.topic-list{position:absolute;left:112px;top:148px;width:500px;list-style:none;color:var(--white)}
.topic-list li{display:flex;gap:14px;font-size:16px;line-height:1.5;margin-bottom:14px}
.topic-list svg{flex:none;margin-top:3px}
.topics .btn{position:absolute;left:112px;top:352px;background:var(--white);color:var(--blue-deep);height:40px;line-height:40px;font-size:14px}
.topic-frame{position:absolute;left:680px;top:40px;width:460px;height:370px;border:2px solid rgba(255,255,255,.7);border-radius:12px}
.topic-photo{position:absolute;left:700px;top:56px;width:440px;height:340px;border-radius:10px;background:linear-gradient(135deg,#c9d6e2 0%,#7f9bb6 55%,#3d5877 100%)}

/* newsletter */
.newsletter{top:2890px;height:280px}
.newsletter .center-title{top:70px}
.subscribe{position:absolute;left:332px;top:150px;width:596px;height:46px;display:flex;border:1px solid var(--pale-2);border-radius:4px;overflow:hidden}
.subscribe .field{flex:1;padding-left:18px;line-height:44px;font-size:14px;color:#9aa3af}
.subscribe .submit{width:128px;background:var(--blue-deep);color:var(--white);font-weight:500;text-align:center;line-height:44px;font-size:15px}

/* footer */
.site-footer{top:3170px;height:422px;background:var(--footer);color:#cfd3da}
.site-footer .brand{position:absolute;left:112px;top:68px;color:var(--white);font-size:30px}
.site-footer .brand-dot{background:var(--blue-bright)}
.follow{position:absolute;left:112px;top:160px;display:flex;align-items:center;gap:12px;font-size:15px;font-weight:700;color:var(--white)}
.follow span{width:34px;height:34px;border-radius:50%;border:1px solid #9aa0a8}
.follow b{margin-right:6px}
.fcol{position:absolute;top:50px}
.fcol h4{font-size:15px;font-weight:700;color:var(--white);margin-bottom:18px;letter-spacing:.4px}
.fcol li{list-style:none;font-size:14px;line-height:26px}
.contact li{display:flex;gap:12px;align-items:center;margin-bottom:10px;line-height:1.3}
.footer-rule{position:absolute;left:112px;right:112px;top:296px;height:1px;background:#3a3c41}
.pay{position:absolute;left:112px;top:326px;display:flex;gap:8px}
.pay span{width:44px;height:28px;border-radius:3px;background:#d7dbe1}
.copyright{position:absolute;left:0;width:1200px;top:368px;text-align:center;font-size:13px;color:#a9aeb6}
</style>
</head>
<body>

<header class="section site-header">
  <div class="brand"><span class="brand-dot"></span>PostNook</div>
  <nav class="nav">
    <span class="active">Home</span>
    <span>About us</span>
    <span>Services</span>
    <span>Plan</span>
    <span>Contact us</span>
    <svg width="18" height="18" viewBox="0 0 18 18"><circle cx="7.5" cy="7.5" r="5.5" fill="none" stroke="#0054AA" stroke-width="2"/><path d="M12 12l4.5 4.5" stroke="#0054AA" stroke-width="2" stroke-linecap="round"/></svg>
    <span class="btn register">Register</span>
  </nav>
</header>

<section class="section hero">
  <div class="hero-photo" role="img" aria-label="Dark blue photo of a hand holding a tablet with glowing data overlays"></div>
  <h1><span class="pre">Welcome to</span><span class="name">PostNook</span></h1>
  <p>The purpose of this platform is to allow anyone to start a blog and automate the process of creating content and posting it to the blog.</p>
  <span class="btn">Sign up for a free trial</span>
  <div class="dots"><span></span><span></span><span></span><span></span></div>
  <svg class="hero-wave" width="1200" height="90" viewBox="0 0 1200 90"><path d="M0 62 C300 86 620 56 1200 10 L1200 90 L0 90Z" fill="#0094D4"/><path d="M0 72 C300 94 620 66 1200 26 L1200 90 L0 90Z" fill="#fff"/></svg>
</section>

<section class="section about">
  <div class="monitor" role="img" aria-label="Desktop monitor showing the blog settings dashboard"></div>
  <h2 class="section-title">About <b>The Platform</b></h2>
  <p>The platform will require a list of blog topics. Based on the topics list, the software will need to automatically send prompts to TextEngine AI in the specified intervals (monthly, weekly, or daily), receive the blog content, and post it to the blog. Furthermore, the software will need some method of adding at least one image to each blog post. Ideally, this would be achieved by using the StockLens API to retrieve images based on keywords in the blog topic.</p>
  <span class="btn">Sign up for a free trial</span>
</section>

<section class="section plans">
  <h2 class="center-title">Our <b>Plans</b></h2>

  <div class="plan" style="left:112px">
    <div class="label">BASE PLAN</div>
    <div class="price">$9.99<small>/Month</small></div>
    <div class="posts">1 blog post (up to 2,000 words)</div>
    <ul>
      <li><svg width="16" height="16" viewBox="0 0 16 16"><circle cx="8" cy="8" r="8" fill="#0094D4"/><path d="M4.5 8.2l2.3 2.3 4.7-4.8" fill="none" stroke="#fff" stroke-width="1.8"/></svg>Lorem ipsum dolor sit amet</li>
      <li><svg width="16" height="16" viewBox="0 0 16 16"><circle cx="8" cy="8" r="8" fill="#0094D4"/><path d="M4.5 8.2l2.3 2.3 4.7-4.8" fill="none" stroke="#fff" stroke-width="1.8"/></svg>Lorem ipsum dolor sit amet</li>
      <li><svg width="16" height="16" viewBox="0 0 16 16"><circle cx="8" cy="8" r="8" fill="#0094D4"/><path d="M4.5 8.2l2.3 2.3 4.7-4.8" fill="none" stroke="#fff" stroke-width="1.8"/></svg>Lorem ipsum dolor sit amet</li>
    </ul>
    <span class="btn">CHOOSE PLAN</span>
  </div>

  <div class="plan featured" style="left:446px">
    <div class="label">PREMIUM PLAN</div>
    <div class="price">$14.99<small>/Week</small></div>
    <div class="posts">1 blog post (up to 2,000 words)</div>
    <ul>
      <li><svg width="16" height="16" viewBox="0 0 16 16"><circle cx="8" cy="8" r="8" fill="#6FCCEA"/><path d="M4.5 8.2l2.3 2.3 4.7-4.8" fill="none" stroke="#0054AA" stroke-width="1.8"/></svg>Lorem ipsum dolor sit amet</li>
      <li><svg width="16" height="16" viewBox="0 0 16 16"><circle cx="8" cy="8" r="8" fill="#6FCCEA"/><path d="M4.5 8.2l2.3 2.3 4.7-4.8" fill="none" stroke="#0054AA" stroke-width="1.8"/></svg>Lorem ipsum dolor sit amet</li>
      <li><svg width="16" height="16" viewBox="0 0 16 16"><circle cx="8" cy="8" r="8" fill="#6FCCEA"/><path d="M4.5 8.2l2.3 2.3 4.7-4.8" fill="none" stroke="#0054AA" stroke-width="1.8"/></svg>Lorem ipsum dolor sit amet</li>
    </ul>
    <span class="btn">CHOOSE PLAN</span>
  </div>

  <div class="plan" style="left:780px">
    <div class="label">ULTIMATE PLAN</div>
    <div class="price">$24.99<small>/Per day</small></div>
    <div class="posts">1 blog post (up to 3,000 words)</div>
    <ul>
      <li><svg width="16" height="16" viewBox="0 0 16 16"><circle cx="8" cy="8" r="8" fill="#0094D4"/><path d="M4.5 8.2l2.3 2.3 4.7-4.8" fill="none" stroke="#fff" stroke-width="1.8"/></svg>Lorem ipsum dolor sit amet</li>
      <li><svg width="16" height="16" viewBox="0 0 16 16"><circle cx="8" cy="8" r="8" fill="#0094D4"/><path d="M4.5 8.2l2.3 2.3 4.7-4.8" fill="none" stroke="#fff" stroke-width="1.8"/></svg>Lorem ipsum dolor sit amet</li>
      <li><svg width="16" height="16" viewBox="0 0 16 16"><circle cx="8" cy="8" r="8" fill="#0094D4"/><path d="M4.5 8.2l2.3 2.3 4.7-4.8" fill="none" stroke="#fff" stroke-width="1.8"/></svg>Lorem ipsum dolor sit amet</li>
    </ul>
    <span class="btn">CHOOSE PLAN</span>
  </div>
</section>

<section class="section benefits">
  <h2 class="center-title">Benefits of <b>Consistent Blogging</b></h2>
  <span class="arrow prev" style="left:56px"><svg width="12" height="12" viewBox="0 0 12 12"><path d="M8 2L4 6l4 4" fill="none" stroke="#0054AA" stroke-width="2"/></svg></span>
  <span class="arrow" style="left:1112px"><svg width="12" height="12" viewBox="0 0 12 12"><path d="M4 2l4 4-4 4" fill="none" stroke="#fff" stroke-width="2"/></svg></span>

  <div class="benefit" style="left:88px">
    <div class="benefit-icon"><span role="img" aria-label="Icon of a blog article page"></span></div>
    <h3>Lorem ipsum do</h3>
    <p>Sed ut perspiciatis unde omnis iste natus error sit voluptatem accusantium</p>
  </div>
  <div class="benefit active" style="left:348px">
    <div class="benefit-icon"><span role="img" aria-label="Icon of a handshake"></span></div>
    <h3>Lorem ipsum do</h3>
    <p>Sed ut perspiciatis unde omnis iste natus error sit voluptatem accusantium</p>
  </div>
  <div class="benefit" style="left:612px">
    <div class="benefit-icon"><span role="img" aria-label="Icon of a content calendar"></span></div>
    <h3>Lorem ipsum do</h3>
    <p>Sed ut perspiciatis unde omnis iste natus error sit voluptatem accusantium</p>
  </div>
  <div class="benefit" style="left:872px">
    <div class="benefit-icon"><span role="img" aria-label="Icon of a website layout"></span></div>
    <h3>Lorem ipsum do</h3>
    <p>Sed ut perspiciatis unde omnis iste natus error sit voluptatem accusantium</p>
  </div>
</section>

<section class="section topics">
  <h2>The Blog Topics <b>Of Methods</b></h2>
  <ul class="topic-list">
    <li><svg width="18" height="18" viewBox="0 0 18 18"><circle cx="9" cy="9" r="9" fill="#fff"/><path d="M5 9.3l2.6 2.6 5.4-5.4" fill="none" stroke="#0054AA" stroke-width="2"/></svg>The user enters them into a table manually.</li>
    <li><svg width="18" height="18" viewBox="0 0 18 18"><circle cx="9" cy="9" r="9" fill="#fff"/><path d="M5 9.3l2.6 2.6 5.4-5.4" fill="none" stroke="#0054AA" stroke-width="2"/></svg>The user uploads a list of blog topics in CSV format.</li>
    <li><svg width="18" height="18" viewBox="0 0 18 18"><circle cx="9" cy="9" r="9" fill="#fff"/><path d="M5 9.3l2.6 2.6 5.4-5.4" fill="none" stroke="#0054AA" stroke-width="2"/></svg>AI can create the list of blog topics based on a prompt such as "Provide a list of 52 blog topics for a handyman business's blog.</li>
  </ul>
  <span class="btn">Learn More</span>
  <div class="topic-frame"></div>
  <div class="topic-photo" role="img" aria-label="Photo of hands typing on a laptop showing a news website"></div>
</section>

<section class="section newsletter">
  <h2 class="center-title">Sign Up <b>Newsletter</b></h2>
  <div class="subscribe"><span class="field">Enter Email ID</span><span class="submit">Submit</span></div>
</section>

<footer class="section site-footer">
  <div class="brand"><span class="brand-dot"></span>PostNook</div>
  <div class="follow"><b>FOLLOW US</b><span></span><span></span><span></span></div>

  <div class="fcol contact" style="left:480px">
    <h4>CONTACT INFO</h4>
    <ul>
      <li><svg width="14" height="16" viewBox="0 0 14 16"><path d="M7 0a6 6 0 0 0-6 6c0 4.5 6 10 6 10s6-5.5 6-10a6 6 0 0 0-6-6zm0 8.5A2.5 2.5 0 1 1 7 3.5a2.5 2.5 0 0 1 0 5z" fill="#0094D4"/></svg><span>PostNook<br>Address Comes Here</span></li>
      <li><svg width="14" height="14" viewBox="0 0 14 14"><path d="M3 0l2.5 3-1.5 2a9 9 0 0 0 5 5l2-1.5 3 2.5-2 3C6 14 0 8 0 2z" fill="#0094D4"/></svg>+1 (555) 014-2270</li>
      <li><svg width="16" height="12" viewBox="0 0 16 12"><rect width="16" height="12" rx="1.5" fill="#0094D4"/><path d="M1 1.5l7 5 7-5" fill="none" stroke="#1f2023" stroke-width="1.4"/></svg>hello@postnook.io</li>
    </ul>
  </div>
  <div class="fcol" style="left:760px">
    <h4>QUICK LINKS</h4>
    <ul><li>Home</li><li>About us</li><li>Services</li><li>Plan</li><li>Contact us</li></ul>
  </div>
  <div class="fcol" style="left:970px">
    <h4>OTHER LINKS</h4>
    <ul><li>Terms &amp; Conditions</li><li>Privacy Policy</li><li>About Us</li><li>Support</li></ul>
  </div>

  <div class="footer-rule"></div>
  <div class="pay"><span></span><span></span><span></span><span></span><span></span></div>
  <div class="copyright">© copyrights 2024 PostNook. All Rights Reserved.</div>
</footer>

</body>
</html>
```